Upmarket Dessert Lounge needs a Business Card Design

We are an upmarket dessert lounge needing a business card to match our image.

We want something that is simple yet beautiful, feminine, classy, sophisticated and elegant. We want it to stand out and don't mind if it is bold.

The design should include our logo and colours of red or maroon with gold highlights. We don't mind if black is used.

Marlow & Quince

Target Market(s)

For those who like to indulge or treat themselves and give in to their temptations on good quality desserts.

Industry/Entity Type

Business

Requirements
Must have
• Must include our logo and our name

Marlow & Quince

M & Q

```html
<!DOCTYPE html>
<html lang="en">
<head>
<meta charset="utf-8">
<title>Marlow &amp; Quince – Business Card</title>
<link rel="stylesheet" href="https://fonts.googleapis.com/css2?family=Cinzel:wght@400&family=Open+Sans:wght@400;700&display=swap">
<style>
  :root {
    --maroon: #7b1416;
    --peach: #fdd39b;
    --cream: #f7e3c4;
    --card-white: #ffffff;
    --backdrop: #e8e2dc;
    --ornament-tint: #fbf3ea;
  }
  * { box-sizing: border-box; margin: 0; padding: 0; }
  html, body { width: 1200px; height: 402px; overflow: hidden; }
  body {
    background: var(--backdrop);
    position: relative;
    font-family: "Open Sans", Arial, sans-serif;
  }
  .card {
    position: absolute;
    top: 56px;
    width: 511px;
    height: 291px;
    border-radius: 12px;
    background: var(--card-white);
    overflow: hidden;
    box-shadow: 0 2px 6px rgba(0,0,0,0.18);
  }
  .card--front { left: 68px; }
  .card--back { left: 627px; }

  .name-band {
    height: 45px;
    background: var(--peach);
    color: var(--maroon);
    text-align: center;
    line-height: 45px;
    font-size: 12px;
  }
  .name-band .person { font-size: 16px; font-weight: 700; }

  .brand-area {
    height: 177px;
    display: flex;
    align-items: center;
    justify-content: center;
  }
  .brand-name {
    font-family: "Cinzel", Georgia, serif;
    font-weight: 400;
    color: var(--maroon);
    font-size: 30px;
    letter-spacing: 1px;
  }

  .contact-band {
    position: absolute;
    left: 0; right: 0; bottom: 0;
    height: 69px;
    background: var(--maroon);
    color: var(--card-white);
    font-size: 12.5px;
    text-align: center;
    padding-top: 7px;
    line-height: 20px;
  }
  .contact-row { display: flex; justify-content: center; gap: 20px; }
  .contact-item { display: inline-flex; align-items: center; gap: 3px; }
  .contact-item svg { width: 11px; height: 11px; fill: none; stroke: var(--card-white); stroke-width: 1.6; }

  .ornament-field {
    position: absolute;
    left: 140px;
    width: 230px;
    height: 60px;
    border-radius: 30px;
    background: var(--ornament-tint);
  }
  .ornament-field--top { top: 30px; }
  .ornament-field--bottom { bottom: 30px; }

  .monogram {
    position: absolute;
    inset: 0;
    display: flex;
    align-items: center;
    justify-content: center;
    font-family: "Cinzel", Georgia, serif;
    font-size: 46px;
    color: var(--maroon);
  }
</style>
</head>
<body>
  <section class="card card--front" aria-label="Business card front">
    <header class="name-band"><span class="person">Your name,</span> Title</header>
    <div class="brand-area">
      <span class="brand-name">MARLOW &amp; QUINCE</span>
    </div>
    <footer class="contact-band">
      <div class="contact-row">
        <span class="contact-item">
          <svg viewBox="0 0 12 12" aria-hidden="true"><circle cx="6" cy="6" r="5"/><path d="M4 3.5 L5 5.5 L4.5 6.5 Q5.5 8 7 8.5 L8 7.5 L9 8.5"/></svg>
          987-654-3210
        </span>
        <span class="contact-item">
          <svg viewBox="0 0 12 12" aria-hidden="true"><rect x="3" y="1" width="6" height="10" rx="1"/><line x1="5" y1="9" x2="7" y2="9"/></svg>
          987-654-3210
        </span>
        <span class="contact-item">
          <svg viewBox="0 0 12 12" aria-hidden="true"><circle cx="6" cy="6" r="5"/><ellipse cx="6" cy="6" rx="2.2" ry="5"/><line x1="1" y1="6" x2="11" y2="6"/></svg>
          www.marlow&amp;quince.com
        </span>
      </div>
      <div>info@marlow&amp;quince.com</div>
      <div>Street Name, City Name, State Zip Code</div>
    </footer>
  </section>

  <section class="card card--back" aria-label="Business card back">
    <div class="ornament-field ornament-field--top" role="img" aria-label="Faint cream flourish ornament above the monogram"></div>
    <div class="ornament-field ornament-field--bottom" role="img" aria-label="Faint cream flourish ornament below the monogram"></div>
    <div class="monogram">M &amp; Q</div>
  </section>
</body>
</html>
```